Business card design needed

A laid back coffee shop that has a great feel, that becomes a bar and grill at night. We are also wanting to cater for functions etc.
The business itself is painted dark blue/charcoal and has red doors.
Would like a logo that will be recognised when seen.

Industry/Entity Type

Coffee Shop

Contact Information for Business Card

The Lantern Coffee Bar & Grill
14b Wattle St
Merrindale NSW 2291
Ph. 02 4817 6230

Logo Text

Logo styles of interest
Emblem Logo
Abstract Logo
Wordmark Logo
Requirements
Must have
• A loyalty card on the back with 2 rows of 7 stamp spaces and a place to write a name and phone number (for a draw)

```html
<!DOCTYPE html>
<html lang="en">
<head>
<meta charset="utf-8">
<title>The Lantern Coffee Bar &amp; Grill — Business Card</title>
<link rel="stylesheet" href="https://fonts.googleapis.com/css2?family=Delius&display=swap">
<style>
  :root {
    --page: #ffffff;
    --card: #ffffff;
    --ink: #1a1a1a;
    --accent: #e0211b;
    --wash-light: rgba(250, 226, 180, 0.35);
    --wash-mid: rgba(240, 190, 110, 0.45);
    --rule: #222222;
  }
  * { box-sizing: border-box; margin: 0; padding: 0; }
  html, body {
    width: 1200px; height: 1000px; overflow: hidden;
    background: var(--page);
    font-family: "Delius", cursive;
    color: var(--ink);
  }
  .card {
    position: absolute; left: 320px; width: 555px; height: 342px;
    background: var(--card); overflow: hidden;
    box-shadow: 0 0 0 1px #ececec;
  }
  .card--front { top: 93px; }
  .card--back { top: 518px; }

  .texture {
    position: absolute; top: 0; bottom: 0; left: 0; width: 480px;
    background: linear-gradient(90deg, transparent 0%, var(--wash-light) 45%, var(--wash-mid) 75%, transparent 100%);
  }

  /* front */
  .brand-mark {
    position: absolute; left: 128px; top: 45px;
    width: 34px; height: 34px; border-radius: 50%;
    background: var(--accent);
  }
  .brand-name {
    position: absolute; left: 10px; width: 270px; top: 228px;
    text-align: center; font-size: 35px; letter-spacing: 1px; line-height: 1;
  }
  .brand-sub {
    position: absolute; left: 10px; width: 270px; top: 270px;
    text-align: center; font-size: 16px; letter-spacing: 0.5px;
  }
  .divider {
    position: absolute; left: 280px; top: 83px;
    width: 2px; height: 180px; background: var(--rule);
  }
  .address {
    position: absolute; left: 292px; width: 220px; top: 96px;
    text-align: center; font-style: normal; font-size: 21px; line-height: 36.5px;
    letter-spacing: 0.5px;
  }

  /* back */
  .stamps {
    position: absolute; left: 25px; top: 32px;
    display: grid; grid-template-columns: repeat(7, 58px);
    column-gap: 15px; row-gap: 11px;
  }
  .stamp {
    width: 58px; height: 58px; border-radius: 50%;
    border: 2px solid var(--ink);
  }
  .entry {
    position: absolute; left: 25px; display: flex; align-items: baseline;
    font-size: 15px;
  }
  .entry__label { width: 90px; }
  .entry__line { width: 327px; border-bottom: 1px dashed var(--ink); height: 12px; }
  .entry--name { top: 192px; }
  .entry--phone { top: 234px; }
  .back-brand {
    position: absolute; left: 0; width: 505px; top: 286px;
    text-align: center; font-size: 17px; letter-spacing: 1px; word-spacing: 3px;
  }
  .back-mark {
    position: absolute; left: 484px; top: 212px;
    width: 26px; height: 26px; border-radius: 50%;
    background: var(--accent);
  }
</style>
</head>
<body>
  <section class="card card--front">
    <div class="texture" role="img" aria-label="Photograph of a coffee cup ring stain"></div>
    <div class="brand-mark" aria-hidden="true"></div>
    <div class="brand-name">THE LANTERN</div>
    <div class="brand-sub">Coffee Bar &amp; Grill</div>
    <div class="divider"></div>
    <address class="address">
      14b Wattle St<br>
      Merrindale<br>
      NSW 2291<br>
      Ph. 02 4817 6230
    </address>
  </section>

  <section class="card card--back">
    <div class="texture" role="img" aria-label="Photograph of a coffee cup ring stain"></div>
    <div class="stamps" aria-label="Loyalty stamps">
      <span class="stamp"></span><span class="stamp"></span><span class="stamp"></span><span class="stamp"></span><span class="stamp"></span><span class="stamp"></span><span class="stamp"></span>
      <span class="stamp"></span><span class="stamp"></span><span class="stamp"></span><span class="stamp"></span><span class="stamp"></span><span class="stamp"></span><span class="stamp"></span>
    </div>
    <div class="entry entry--name"><span class="entry__label">Name</span><span class="entry__line"></span></div>
    <div class="entry entry--phone"><span class="entry__label">Phone</span><span class="entry__line"></span></div>
    <div class="back-brand">THE LANTERN Coffee Bar &amp; Grill</div>
    <div class="back-mark" aria-hidden="true"></div>
  </section>
</body>
</html>
```